Website Redesign Brief for Tallowmere Climate Services WA

Creating a clear and concise brief for designers to redesign your website, https://breezelineclimatewa.com.au/, is essential to ensure the project aligns with your vision for a more energetic, friendly, optimistic, and user-friendly website. Below is a sample brief tailored to your request, balancing specificity with flexibility to allow designers to bring their creativity to the table.

Website Redesign Brief for Tallowmere Climate WA
1. Project Overview

We are seeking a redesign of our website, https://breezelineclimatewa.com.au/, to create a vibrant, engaging, and user-friendly online presence that reflects our brand’s commitment to providing top-notch air conditioning services in Western Australia. The redesigned website should feel energetic, friendly, and optimistic while maintaining professionalism and improving user experience.
2. Goals and Objectives

Enhance Brand Perception: Convey a modern, approachable, and positive brand identity that resonates with both residential and commercial clients.
Improve User Experience: Simplify navigation, improve accessibility, and ensure a seamless experience across devices (desktop, tablet, mobile).
Increase Engagement: Encourage visitors to explore services, request quotes, and contact us through clear calls-to-action (CTAs).
Boost Conversion Rates: Make it easier for users to find information and take action (e.g., booking services or inquiries).
Showcase Expertise: Highlight our professional air conditioning services, experience, and customer satisfaction in an inviting way.

3. Target Audience

Primary Audience: Homeowners and small business owners in Western Australia seeking air conditioning installation, maintenance, or repair services.
Secondary Audience: Property managers, commercial clients, and real estate professionals looking for reliable HVAC solutions.
Demographics: Ages 25–65, mix of tech-savvy and non-tech-savvy users, located primarily in Perth and surrounding areas.
User Needs: Clear information about services, transparent pricing, easy contact options, and reassurance of quality and reliability.

4. Design Preferences

Tone and Style:

Energetic: Use bold, vibrant colors (e.g., blues, whites, and pops of warm tones like orange or yellow) to evoke energy and optimism.
Friendly: Incorporate approachable language, welcoming imagery, and a clean, uncluttered layout.
Optimistic: Highlight positive customer outcomes (e.g., comfort, energy savings) through visuals and messaging.
Professional yet approachable: Maintain credibility as a trusted service provider while avoiding a cold or overly corporate feel.

Visual Elements:

Use high-quality images of happy customers, comfortable homes/offices, and modern air conditioning units.
Incorporate subtle animations or micro-interactions to add energy (e.g., hover effects on buttons or smooth scrolling).
Avoid overly complex graphics that may slow down the site or distract from usability.

Typography: Clean, modern fonts that are easy to read. Use larger, bold headings for hierarchy and warmth.
Inspiration: Websites like https://www.vorlex.com.au/ (clean and professional) or https://www.tandoraclimatech.com.au/ (user-friendly and modern) but with a more vibrant and welcoming vibe.

5. Functional Requirements

User-Friendly Navigation: Simplify the menu structure to make key pages (e.g., Services, About Us, Contact) easily accessible.
Mobile Responsiveness: Ensure the site is fully optimized for mobile devices, with fast load times and intuitive touch interactions.
Key Features:

Prominent CTAs for requesting quotes, booking services, or contacting the team.
A clear service overview with icons or visuals for each service (e.g., installation, repairs, maintenance).
A testimonials section to showcase customer satisfaction.
An easy-to-use contact form with minimal fields.
Integration with Google Maps for location-based services or office directions.

SEO and Performance: Optimize for search engines (e.g., keywords like “air conditioning Perth”) and ensure fast loading speeds.
Accessibility: Follow WCAG guidelines to ensure the site is usable for all visitors, including those with disabilities.

6. Content Guidance

Existing Content: Review and refine current content from https://breezelineclimatewa.com.au/ to make it concise, engaging, and aligned with the friendly tone.
New Content Ideas:

Add a “Why Choose Us” section highlighting expertise, customer service, and eco-friendly solutions.
Include a FAQ page to address common customer questions.
Create a blog section for tips on air conditioning maintenance or energy efficiency (optional).

Tone of Voice: Conversational, reassuring, and positive. Avoid technical jargon unless clearly explained.

7. Technical Considerations

Platform: Open to recommendations (e.g., WordPress, Wix, or custom-built) but prioritize ease of maintenance and scalability.
Integrations: Ensure compatibility with existing tools (e.g., Google Analytics, CRM for quote requests, or booking systems).
Domain and Hosting: Retain current domain (tallowmereclimatewa.com.au); hosting recommendations welcome.
Timeline: Initial design concepts within [insert timeline, e.g., 2–3 weeks], with full redesign completed by [insert deadline, e.g., 6–8 weeks].
Budget: [Insert budget range or state “flexible, please provide a quote”].

8. Deliverables

Wireframes and mockups for homepage, service pages, and contact page.
Fully responsive website design with all necessary pages.
Style guide (colors, fonts, imagery guidelines).
CMS setup (if applicable) with basic training for content updates.
Testing and optimization for performance and SEO.

9. Success Metrics

Increased time on site and reduced bounce rate.
Higher conversion rates for quote requests and contact form submissions.
Positive user feedback on ease of navigation and overall experience.
Improved search engine rankings for key terms within [insert timeframe, e.g., 3 months].

10. Additional Notes

Please provide a portfolio of similar projects or examples of user-friendly, vibrant websites.
We are open to creative suggestions to make the website stand out in the HVAC industry.
Regular progress updates and collaboration during the design process are appreciated.
Updates

designers are asking for more time

few have requested an extension. I Have extended

Target Market(s)

Primary Audience: Homeowners and small business owners in Western Australia seeking air conditioning installation, maintenance, or repair services. Secondary Audience: Property managers, commercial clients, and real estate professionals looking for reliable HVAC solutions. Demographics: Ages 25–65, mix of tech-savvy and non-tech-savvy users, located primarily in Perth and surrounding areas. User Needs: Clear information about services, transparent pricing, easy contact options, and reassurance of quality and reliability.

Industry/Entity Type

Air Conditioning and Refrigeration (HVAC & R)

Coding

Coded - Design and coding required

Colors
0054AA
0677BA
7BADD7
CADEEF
E8F1F8
59FF00
82FF00
B8FF75
E3FFCB
F4FFEA
F0912C
F2A743
F7CA91
FBE8D2
FDF5EE
EE7325
F08F49
F5BC92
FAE3D3
FDF4ED

Requirements
Must have
• Must have all my current information I currently have on my web page.
Nice to have
• A sales page for people to buy products online

```html
<!DOCTYPE html>
<html lang="en">
<head>
<meta charset="utf-8">
<title>Tallowmere Climate Services WA</title>
<link href="https://fonts.googleapis.com/css2?family=Roboto:wght@300;400;500;700;900&family=Montserrat:wght@300;400;500;600&display=swap" rel="stylesheet">
<style>
:root{
  --red:#e3202a;
  --red-dark:#c8151d;
  --orange:#ee7325;
  --orange-light:#f0912c;
  --navy:#262b62;
  --navy-deep:#1b1f4d;
  --ink:#1c1c1c;
  --text:#444;
  --muted:#8a8a8a;
  --grey-bg:#f3f3f3;
  --cream:#fdf0d9;
  --white:#fff;
  --black:#0c0c0c;
}
*{box-sizing:border-box;margin:0;padding:0}
html,body{width:1200px;height:5119px;overflow:hidden}
body{position:relative;font-family:'Roboto',sans-serif;color:var(--ink);background:var(--white)}
.abs{position:absolute}
section,header,footer{position:absolute;left:0;width:1200px;overflow:hidden}
.btn{position:absolute;display:flex;align-items:center;justify-content:center;color:#fff;font:500 14px 'Roboto',sans-serif;border-radius:6px;background:linear-gradient(90deg,var(--red),var(--orange))}
.label{position:absolute;left:0;width:100%;text-align:center;font:500 13px 'Roboto',sans-serif;text-transform:uppercase;letter-spacing:.3px}
.title{position:absolute;left:0;width:100%;text-align:center;font:700 36px 'Roboto',sans-serif;text-transform:uppercase}
.img{position:absolute}

/* header */
.site-header{top:0;height:124px;background:transparent;overflow:visible;z-index:2}
.header-bg{position:absolute;left:0;top:0;width:1200px;height:108px;background:var(--white)}
.topbar-info{position:absolute;left:462px;top:22px;font:400 13px 'Roboto',sans-serif;color:var(--ink);display:flex;gap:10px;align-items:center}
.topbar-info svg{vertical-align:-2px;margin-right:6px}
.navbar{position:absolute;left:0;top:60px;width:960px;height:48px;background:var(--red)}
.nav-links{position:absolute;left:334px;top:76px;font:400 13px 'Roboto',sans-serif;color:#fff}
.nav-links span{position:absolute;white-space:nowrap}
.call-block{position:absolute;left:930px;top:0;width:270px;height:108px;background:var(--navy-deep);clip-path:polygon(40px 0,100% 0,100% 100%,0 100%)}
.call-icon{position:absolute;left:976px;top:16px}
.call-label{position:absolute;left:1030px;top:25px;color:#fff;font:500 14px 'Roboto',sans-serif}
.call-number{position:absolute;left:950px;top:62px;color:#fff;font:500 26px 'Roboto',sans-serif;letter-spacing:.3px}
.brand-badge{position:absolute;left:150px;top:0;width:162px;height:124px;background:#fff;border-radius:0 0 80px 80px;box-shadow:0 4px 10px rgba(0,0,0,.15);display:flex;align-items:center;justify-content:center;text-align:center;padding:0 18px;font:700 13px 'Roboto',sans-serif;color:var(--red);line-height:1.25}

/* hero */
.hero{top:108px;height:442px;background:#0f0f0f}
.hero-photo{left:420px;top:0;width:780px;height:442px;background:linear-gradient(100deg,#1a1613 0%,#8a6e58 30%,#d8c5b4 60%,#efe6dc 100%)}
.hero-shade{position:absolute;left:0;top:0;width:800px;height:442px;background:linear-gradient(90deg,rgba(10,10,10,1) 40%,rgba(10,10,10,0) 100%)}
.hero-kicker{position:absolute;left:152px;top:76px;font:300 36px 'Roboto',sans-serif;color:var(--orange-light);letter-spacing:.3px}
.hero-title{position:absolute;left:152px;top:122px;font:700 36px/48px 'Roboto',sans-serif;color:#fff;text-transform:uppercase}
.hero-text{position:absolute;left:152px;top:234px;width:390px;font:400 12px/19px 'Roboto',sans-serif;color:#fff}

/* about */
.about{top:550px;height:562px;background:#fff}
.about-art{left:80px;top:40px;width:520px;height:522px;background:radial-gradient(circle at 50% 45%,#3b5fb8 0%,#243d86 35%,#f4ede6 70%,#fff 100%)}
.about-kicker{position:absolute;left:680px;top:168px;font:500 13px 'Roboto',sans-serif;color:var(--navy)}
.about-title{position:absolute;left:680px;top:188px;font:700 36px 'Roboto',sans-serif;color:var(--red)}
.about-text{position:absolute;left:680px;top:252px;width:380px;font:400 14px/22px 'Roboto',sans-serif;color:var(--text)}

/* services */
.services{top:1112px;height:688px;background:var(--grey-bg)}
.services-intro{position:absolute;left:250px;width:700px;top:172px;text-align:center;font:400 14px/20px 'Roboto',sans-serif;color:var(--ink)}
.service-card{position:absolute;top:258px;width:258px;height:266px;background:#fff}
.service-card .img{left:0;top:0;width:258px;height:194px}
.service-card h3{position:absolute;left:0;width:100%;top:212px;text-align:center;font:500 15px 'Roboto',sans-serif}
.go{position:absolute;top:500px;width:34px;height:34px;border-radius:50%;background:var(--red);display:flex;align-items:center;justify-content:center}
.slide-arrow{position:absolute;top:334px;width:36px;height:36px;border-radius:50%;background:var(--navy);display:flex;align-items:center;justify-content:center}

/* why */
.why{top:1800px;height:596px;background:#fff}
.why-intro{position:absolute;left:260px;width:680px;top:208px;text-align:center;font:400 14px/20px 'Roboto',sans-serif;color:var(--ink)}
.why-item h4{position:absolute;font:600 14px 'Roboto',sans-serif;color:var(--ink)}
.why-item p{position:absolute;width:320px;font:400 11px/18px 'Montserrat',sans-serif;color:var(--muted)}
.why-item .r{text-align:right}
.why-icon{position:absolute;width:88px;height:88px;border-radius:50%;background:linear-gradient(135deg,var(--orange),var(--red));display:flex;align-items:center;justify-content:center;box-shadow:0 0 0 6px #fff}
.why-brand{position:absolute;left:490px;top:460px;width:228px;text-align:center;font:700 20px 'Roboto',sans-serif;color:var(--red);line-height:1.2}

/* testimonials */
.testimonials{top:2396px;height:460px;background:linear-gradient(90deg,#252a62,#2d3270 50%,#252a62)}
.quote{position:absolute;left:270px;width:660px;top:220px;text-align:center;font:300 15px/26px 'Montserrat',sans-serif;color:#c9cbe0}
.quote-name{position:absolute;left:0;width:100%;top:318px;text-align:center;font:500 22px 'Montserrat',sans-serif;color:#fff;letter-spacing:.5px}
.dots{position:absolute;left:549px;top:366px;display:flex;gap:9px}
.dots i{width:13px;height:13px;border-radius:50%;border:1.5px solid #fff;display:block}
.dots i.on{background:#2e8bff;border-color:#2e8bff}

/* blog */
.blog{top:2856px;height:670px;background:#fff}
.blog-card{position:absolute;top:218px;width:346px;height:340px}
.blog-card.active{background:#fff;box-shadow:0 4px 14px rgba(0,0,0,.12)}
.blog-card .img{left:0;top:0;width:346px;height:202px}
.date{position:absolute;right:0;top:184px;width:110px;height:34px;border-radius:18px 0 0 18px;background:var(--navy);color:#fff;font:500 13px 'Roboto',sans-serif;display:flex;align-items:center;justify-content:center}
.blog-card h3{position:absolute;left:50px;top:222px;font:700 20px 'Roboto',sans-serif;color:var(--ink)}
.blog-card .bar{position:absolute;left:26px;top:218px;width:2px;height:34px;background:var(--orange)}
.blog-card p{position:absolute;left:50px;top:256px;width:270px;font:400 12px/19px 'Roboto',sans-serif;color:#666}

/* consultation */
.consult{top:3526px;height:554px;background:linear-gradient(90deg,#23285e,#2b3070 50%,#23285e)}
.field{position:absolute;background:#fff;font:500 12px 'Roboto',sans-serif;color:var(--ink);padding:22px 18px}

/* faq */
.faq{top:4080px;height:610px;background:#fff}
.faq-title{position:absolute;left:0;width:100%;top:118px;text-align:center;font:500 36px 'Roboto',sans-serif;color:var(--red)}
.faq-item{position:absolute;left:152px;width:904px;height:44px;border:1.5px solid #d9d9e3;border-radius:8px;box-shadow:0 2px 4px rgba(0,0,0,.06);font:500 15px 'Roboto',sans-serif;color:var(--ink);padding:12px 22px}
.faq-item .sign{position:absolute;right:20px;top:10px;font:700 18px 'Roboto',sans-serif}
.faq-item.open{height:114px}
.faq-item.open p{margin-top:14px;font:400 10.5px/17px 'Montserrat',sans-serif;color:#777}
.faq-item.open .sign{color:var(--orange)}

/* footer */
.site-footer{top:4690px;height:429px;background:var(--black);color:#fff}
.footer-brand{position:absolute;left:164px;top:150px;width:262px;font:700 22px 'Roboto',sans-serif;color:var(--red);line-height:1.2;text-align:center}
.footer-head{position:absolute;top:110px;font:500 18px 'Roboto',sans-serif}
.quick-links{position:absolute;left:522px;top:150px;list-style:none;font:400 13px/23px 'Roboto',sans-serif}
.quick-links li::before{content:'»';color:var(--orange);margin-right:10px}
.contact-line{position:absolute;left:802px;font:400 13px 'Roboto',sans-serif;display:flex;align-items:center;gap:12px}
.footer-rule{position:absolute;left:152px;top:342px;width:904px;height:1px;background:#555}
.legal{position:absolute;left:0;width:100%;text-align:center;font:400 11px 'Roboto',sans-serif}
</style>
</head>
<body>

<section class="hero">
  <div class="img hero-photo" role="img" aria-label="Smiling woman giving a thumbs up in a bright room"></div>
  <div class="hero-shade"></div>
  <div class="hero-kicker">QUALITY AIR CONDITIONING</div>
  <h1 class="hero-title">Repairs, Service, and<br>Installations</h1>
  <p class="hero-text">Our service is second to none; we have a team of experienced technicians that consistently deliver the best quality air conditioner repairs Perth has to offer.</p>
  <div class="btn" style="left:152px;top:310px;width:140px;height:36px">Find A Dealer</div>
</section>

<header class="site-header">
  <div class="header-bg"></div>
  <div class="topbar-info">
    <span><svg width="12" height="12" viewBox="0 0 24 24"><path fill="#1c1c1c" d="M6.6 10.8a15 15 0 0 0 6.6 6.6l2.2-2.2c.3-.3.7-.4 1-.2 1.1.4 2.3.6 3.6.6.6 0 1 .4 1 1V20c0 .6-.4 1-1 1A17 17 0 0 1 3 4c0-.6.4-1 1-1h3.5c.6 0 1 .4 1 1 0 1.2.2 2.4.6 3.6.1.3 0 .7-.2 1z"/></svg>Mon-Fri: 8.00am to 5.00pm</span>
    <span>/</span>
    <span><svg width="13" height="11" viewBox="0 0 24 18"><path fill="#1c1c1c" d="M0 0h24v18H0zM2 2v1l10 7 10-7V2z"/></svg>info@tallowmereclimatewa.com.au</span>
  </div>
  <div class="navbar"></div>
  <nav class="nav-links">
    <span style="left:0">Home</span>
    <span style="left:60px">About Us</span>
    <span style="left:138px">Services</span>
    <span style="left:210px">Cleaning</span>
    <span style="left:286px">Regasing</span>
    <span style="left:362px">Commissioning</span>
    <span style="left:476px">Air Balancing</span>
  </nav>
  <div class="call-block"></div>
  <svg class="call-icon" width="40" height="40" viewBox="0 0 40 40"><circle cx="20" cy="20" r="19" fill="var(--orange)"/><circle cx="20" cy="20" r="13" fill="none" stroke="#fff" stroke-width="1.5"/><path fill="#fff" d="M15.5 17.5a9 9 0 0 0 4 4l1.4-1.4c.2-.2.5-.2.7-.1l2.2.5c.3 0 .5.3.5.6v2c0 .4-.3.7-.6.7A10 10 0 0 1 13.2 13.6c0-.3.3-.6.7-.6h2c.3 0 .6.2.6.5l.4 2.2c.1.2 0 .5-.2.7z"/></svg>
  <div class="call-label">Call Us Today</div>
  <div class="call-number">0400 118 392</div>
  <div class="brand-badge">Tallowmere Climate Services WA</div>
</header>

<section class="about">
  <div class="img about-art" role="img" aria-label="Technician in a blue hard hat and work uniform"></div>
  <div class="about-kicker">ABOUT</div>
  <h2 class="about-title">NEED A TECHNICIAN?</h2>
  <p class="about-text">Our call out fee includes the first half hour on site. In most cases will be able to diagnose the problem with in that time, and repair it if no parts are required. If any parts, gas or additional labour is required, we will let you know before we proceed</p>
  <div class="btn" style="left:680px;top:392px;width:140px;height:38px">More About Us</div>
</section>

<section class="services">
  <div class="label" style="top:94px;color:var(--navy)">Some of our speciality</div>
  <h2 class="title" style="top:124px;color:var(--red)">Our Services</h2>
  <p class="services-intro">Please Be aware that paying for your service upfront does not mean next day service. Your service will however be prioritised and scheduled into the next available slot.</p>
  <div class="service-card" style="left:70px"><div class="img" role="img" aria-label="Worker installing commercial ducting" style="background:linear-gradient(160deg,#6f7a86,#b8bec6 55%,#8b7a6a)"></div><h3>Commercial Installattion</h3></div>
  <div class="service-card" style="left:340px"><div class="img" role="img" aria-label="Technician fitting a wall air conditioner" style="background:linear-gradient(160deg,#d9d9d9,#f2f2f2 50%,#4a4f5a)"></div><h3>Domestic Aircon Installation</h3></div>
  <div class="service-card" style="left:610px"><div class="img" role="img" aria-label="Interior of a coolroom with shelving" style="background:linear-gradient(180deg,#6a95b5,#a9c8dc 50%,#5d86a6)"></div><h3>Coolroom Installation &amp; Repairs</h3></div>
  <div class="service-card" style="left:880px"><div class="img" role="img" aria-label="Technician working on overhead ducts" style="background:linear-gradient(160deg,#8a8f96,#3c3f45 60%,#a0a4aa)"></div><h3>Air Quality Control</h3></div>
  <div class="go" style="left:182px"><svg width="12" height="12" viewBox="0 0 12 12"><path d="M4 2l4 4-4 4" fill="none" stroke="#fff" stroke-width="2"/></svg></div>
  <div class="go" style="left:452px"><svg width="12" height="12" viewBox="0 0 12 12"><path d="M4 2l4 4-4 4" fill="none" stroke="#fff" stroke-width="2"/></svg></div>
  <div class="go" style="left:722px"><svg width="12" height="12" viewBox="0 0 12 12"><path d="M4 2l4 4-4 4" fill="none" stroke="#fff" stroke-width="2"/></svg></div>
  <div class="go" style="left:992px"><svg width="12" height="12" viewBox="0 0 12 12"><path d="M4 2l4 4-4 4" fill="none" stroke="#fff" stroke-width="2"/></svg></div>
  <div class="slide-arrow" style="left:52px"><svg width="12" height="12" viewBox="0 0 12 12"><path d="M8 2L4 6l4 4" fill="none" stroke="#fff" stroke-width="2"/></svg></div>
  <div class="slide-arrow" style="left:1118px"><svg width="12" height="12" viewBox="0 0 12 12"><path d="M4 2l4 4-4 4" fill="none" stroke="#fff" stroke-width="2"/></svg></div>
  <div class="btn" style="left:530px;top:580px;width:140px;height:38px">View All Services</div>
</section>

<section class="why">
  <div class="label" style="top:122px;color:var(--navy)">Our speciality</div>
  <h2 class="title" style="top:150px;color:var(--red)">Why Choose Us</h2>
  <p class="why-intro">Please Be aware that paying for your service upfront does not mean next day service. Your service will however be prioritised and scheduled into the next available slot.</p>
  <svg class="abs" style="left:388px;top:282px" width="432" height="432" viewBox="0 0 432 432"><circle cx="216" cy="216" r="198" fill="none" stroke="var(--cream)" stroke-width="18"/></svg>
  <div class="why-brand">Tallowmere Climate Services WA</div>

  <div class="why-item">
    <h4 style="left:324px;top:300px">Affordability</h4>
    <p class="r" style="left:86px;top:322px">Lorem ipsum dolor sit amet, consectetur adipiscing elit, sed do eiusmod tempor incididunt ut labore et dolore magna aliqua</p>
    <h4 style="left:818px;top:300px">Community Focus</h4>
    <p style="left:818px;top:322px">Lorem ipsum dolor sit amet, consectetur adipiscing elit, sed do eiusmod tempor incididunt ut labore et dolore magna aliqua</p>
    <h4 style="left:236px;top:444px">Quality Service</h4>
    <p class="r" style="left:30px;top:466px">Lorem ipsum dolor sit amet, consectetur adipiscing elit, sed do eiusmod tempor incididunt ut labore et dolore magna aliqua</p>
    <h4 style="left:842px;top:446px">Customer Satisfaction</h4>
    <p style="left:848px;top:468px">Lorem ipsum dolor sit amet, consectetur adipiscing elit, sed do eiusmod tempor incididunt ut labore et dolore magna aliqua</p>
  </div>
  <div class="why-icon" style="left:434px;top:310px"><svg width="40" height="40" viewBox="0 0 40 40" fill="none" stroke="#fff" stroke-width="2"><rect x="12" y="6" width="16" height="14" rx="2"/><text x="20" y="17" fill="#fff" stroke="none" font-size="10" text-anchor="middle" font-family="Roboto,sans-serif">$</text><path d="M6 30c4-4 8-4 12-2h8c2 0 2 3 0 3h-8M6 34h22l8-6"/></svg></div>
  <div class="why-icon" style="left:714px;top:310px"><svg width="40" height="40" viewBox="0 0 40 40" fill="none" stroke="#fff" stroke-width="2"><circle cx="20" cy="20" r="16"/><circle cx="20" cy="16" r="4"/><circle cx="11" cy="19" r="3"/><circle cx="29" cy="19" r="3"/><path d="M12 30c2-6 14-6 16 0"/></svg></div>
  <div class="why-icon" style="left:380px;top:452px"><svg width="40" height="40" viewBox="0 0 40 40" fill="none" stroke="#fff" stroke-width="2"><circle cx="20" cy="14" r="8"/><path d="M16 14l3 3 5-6M8 30c4-4 8-4 12-1 4-3 8-3 12 1M8 36h24"/></svg></div>
  <div class="why-icon" style="left:746px;top:456px"><svg width="40" height="40" viewBox="0 0 40 40" fill="none" stroke="#fff" stroke-width="2"><path d="M10 36V22h6v14zM16 24l6-10c2-2 4 0 3 2l-2 5h8c2 0 3 2 2 4l-3 9c-1 2-2 2-4 2H16"/><path d="M9 8l1.5 3 3 .4-2.2 2 .6 3L9 15l-2.9 1.4.6-3-2.2-2 3-.4zM30 4l1 2 2 .3-1.5 1.4.4 2L30 8.8l-1.9.9.4-2L27 6.3l2-.3z"/></svg></div>
</section>

<section class="testimonials">
  <div class="label" style="top:116px;color:var(--orange)">Testimonials</div>
  <h2 class="title" style="top:146px;color:#fff">Customers Say</h2>
  <svg class="abs" style="left:198px;top:238px" width="30" height="14" viewBox="0 0 30 14"><path d="M29 7H3M8 2L2 7l6 5" fill="none" stroke="#fff" stroke-width="2.4"/></svg>
  <svg class="abs" style="left:994px;top:238px" width="30" height="14" viewBox="0 0 30 14"><path d="M1 7h26M22 2l6 5-6 5" fill="none" stroke="#fff" stroke-width="2.4"/></svg>
  <p class="quote">Sed ut perspiciatis unde omnis iste natus error sit voluptatem accusantium doloremque laudantium, totam rem aperiam, eaque ipsa quae ab illo inventore veritatis et quasi architecto beatae vitae dicta sunt explicabo.</p>
  <div class="quote-name">- Mara Ellison</div>
  <div class="dots"><i></i><i></i><i class="on"></i><i></i><i></i></div>
</section>

<section class="blog">
  <div class="label" style="top:112px;color:var(--orange)">Testimonials</div>
  <h2 class="title" style="top:134px;color:var(--red)">Our Blog</h2>
  <article class="blog-card active" style="left:64px">
    <div class="img" role="img" aria-label="Two technicians servicing an outdoor unit" style="background:linear-gradient(160deg,#dfe6ee,#8aa3c4 55%,#2f4f86)"></div>
    <div class="date">AUG 19</div><span class="bar"></span>
    <h3>Nemo enim ipsam</h3>
    <p>Lorem ipsum dolor sit amet, consectetur adipiscing elit, sed do eiusmod tempor incididunt ut labore et dolore magna aliqua.</p>
  </article>
  <article class="blog-card" style="left:428px">
    <div class="img" role="img" aria-label="Technician beside an air conditioning unit" style="background:linear-gradient(160deg,#cfd3d8,#6d7785 50%,#2a3d78)"></div>
    <div class="date">AUG 19</div><span class="bar"></span>
    <h3>Duis aute irure dolor</h3>
    <p>Lorem ipsum dolor sit amet, consectetur adipiscing elit, sed do eiusmod tempor incididunt ut labore et dolore magna aliqua.</p>
  </article>
  <article class="blog-card" style="left:792px">
    <div class="img" role="img" aria-label="Gloved hands servicing a split system unit" style="background:linear-gradient(160deg,#f1f1f1,#d4d6d8 55%,#3a3a3a)"></div>
    <span class="bar"></span>
    <h3>Excepteur sint occaecat</h3>
    <p>Lorem ipsum dolor sit amet, consectetur adipiscing elit, sed do eiusmod tempor incididunt ut labore et dolore magna aliqua.</p>
  </article>
</section>

<section class="consult">
  <div class="label" style="top:76px;color:var(--orange)">Get in touch</div>
  <h2 class="title" style="top:98px;color:#fff">Request A Free Consultation</h2>
  <div class="field" style="left:236px;top:166px;width:358px;height:58px">First Name</div>
  <div class="field" style="left:626px;top:166px;width:358px;height:58px">Last Name</div>
  <div class="field" style="left:236px;top:244px;width:358px;height:56px">Phone Number</div>
  <div class="field" style="left:626px;top:244px;width:358px;height:56px">Email</div>
  <div class="field" style="left:236px;top:320px;width:748px;height:102px">Messages</div>
  <div class="btn" style="left:532px;top:448px;width:140px;height:36px">Send Now</div>
</section>

<section class="faq">
  <div class="label" style="top:78px;color:var(--orange)">FAQ</div>
  <h2 class="faq-title">Frequently Asked Questions</h2>
  <div class="faq-item open" style="top:202px">Lorem ipsum dolor sit amet, consectetur ?<span class="sign">–</span>
    <p>Sed ut perspiciatis unde omnis iste natus error sit voluptatem accusantium doloremque laudantium, totam rem aperiam, eaque ipsa quae ab illo inventore veritatis et quasi architecto beatae vitae dicta sunt explicabo. Nemo enim ipsam voluptatem quia voluptas sit aspernatur aut odit aut fugit, sed quia consequuntur magni dolores eos qui ratione voluptatem sequi nesciunt. Neque porro quisquam est, qui dolorem ipsum quia</p>
  </div>
  <div class="faq-item" style="top:332px">Lorem ipsum dolor sit amet ?<span class="sign">+</span></div>
  <div class="faq-item" style="top:392px">Lorem ipsum dolor sit amet ?<span class="sign">+</span></div>
  <div class="faq-item" style="top:452px">Lorem ipsum dolor sit amet ?<span class="sign">+</span></div>
  <div class="faq-item" style="top:514px">Lorem ipsum dolor sit amet ?<span class="sign">+</span></div>
</section>

<footer class="site-footer">
  <div class="footer-brand">Tallowmere Climate Services WA</div>
  <h3 class="footer-head" style="left:514px">QUICK LINKS</h3>
  <ul class="quick-links">
    <li>Home</li><li>About</li><li>Service</li><li>Project Works</li><li>Residential Services</li><li>Careers</li><li>Contact</li>
  </ul>
  <h3 class="footer-head" style="left:784px">GET IN TOUCH</h3>
  <div class="contact-line" style="top:158px"><svg width="12" height="16" viewBox="0 0 12 16"><path fill="var(--orange)" d="M6 0a6 6 0 0 1 6 6c0 4-6 10-6 10S0 10 0 6a6 6 0 0 1 6-6zm0 4a2 2 0 1 0 0 4 2 2 0 0 0 0-4z"/></svg>42 Harbour Lane, Jandakot WA 6164</div>
  <div class="contact-line" style="top:220px"><svg width="12" height="12" viewBox="0 0 24 24"><path fill="var(--orange)" d="M6.6 10.8a15 15 0 0 0 6.6 6.6l2.2-2.2c.3-.3.7-.4 1-.2 1.1.4 2.3.6 3.6.6.6 0 1 .4 1 1V20c0 .6-.4 1-1 1A17 17 0 0 1 3 4c0-.6.4-1 1-1h3.5c.6 0 1 .4 1 1 0 1.2.2 2.4.6 3.6.1.3 0 .7-.2 1z"/></svg>0400 118 392</div>
  <div class="contact-line" style="top:274px"><svg width="14" height="11" viewBox="0 0 24 18"><path fill="var(--orange)" d="M0 0h24v18H0zM2 2v1l10 7 10-7V2z"/></svg>info@tallowmereclimatewa.com.au</div>
  <div class="footer-rule"></div>
  <div class="legal" style="top:372px">Terms &amp; Conditions / Privacy Policy / Contact Us</div>
  <div class="legal" style="top:406px;font-size:12px">Copyright © 2025, Tallowmere Climate Services WA All Right Reserved</div>
</footer>

</body>
</html>
```